Design a clean homepage for a travel portal based in the US catering to Asians. The design should be able to be used on other pages, or color scheme menu layout, header and footer should be usable on other pages.

Include the main options for users to click, as an example some could be; 1. Local Tour Company 2. Local Tour Guide 3. Transportation Company 4. Tour Packages

Think like www.craftmingle.net who brings designers and clients together we are bringing Tour company, Tour guide, Bus/Transportation company directly to those who need it. This is for a two way portal, not a common one way portal like regular booking sites.

Assume that a person arrives or is planning on arriving at a destination, what are some options that should be on the page, layout of the options: squares, rectangles, stars, scroll slides, whatever makes you feel fun, elegant, fresh, uplifting.

Feelings we want to convey: fun, elegant, fresh, uplifting, interesting, energetic

Update:
When we said this should be a simple design, we meant simple for the end user to understand what was going on. I have attached a screenshot of a website, that it is very easy to understand what its purpose is.

How you decide to set up picture/scenery areas, logo area, menu area, where the options go is all up to you. Would like it to be clean and inviting, we would also like the options to be colors that call the users to action(make them click). This doesn't have to be colors so much as design. If you have further questions feel free to message me.

Attached is our logo in various styles for you to choose from.

Target Market(s)

Travel, package tours, international students, business trips

Industry/Entity Type

Travel Industry

Number of Pages Required

1 page

Colors
ec1f27
ffffff
0255a3
474747
7f7f7f
5c5c5c
aaaaaa

Requirements
Must have
• 1. Local Tour Company 2. Local Tour Guide 3. Transportation Company 4. Tour Packages
Should not have
• Our main goal is not to sell flights or hotel rooms, so this can be an element on the page(or not) but it should not be very central/obvious.

```html
<!DOCTYPE html>
<html lang="en">
<head>
<meta charset="utf-8">
<title>Voyalia – Travel Portal</title>
<link rel="stylesheet" href="https://fonts.googleapis.com/css2?family=Raleway:wght@500;600;700;800&family=Open+Sans:ital,wght@0,400;0,600;0,700;1,400&display=swap">
<style>
:root{
  --red:#ec1f27;
  --red-band:#ec4346;
  --blue:#1b82c5;
  --blue-dark:#0f6aa8;
  --blue-deep:#0255a3;
  --white:#ffffff;
  --ink:#474747;
  --grey:#7f7f7f;
  --grey-mid:#5c5c5c;
  --grey-light:#aaaaaa;
  --line:#e4e4e4;
  --star:#e9a825;
}
*{box-sizing:border-box;margin:0;padding:0}
html,body{width:1200px;height:2320px;overflow:hidden;background:var(--white)}
body{font-family:"Open Sans",Arial,sans-serif;color:var(--ink);position:relative}
a{color:inherit;text-decoration:none}
.section{position:absolute;left:0;width:1200px}
/* top bar */
.topbar{top:0;height:42px;background:var(--blue);color:var(--white);font-size:11px;text-transform:uppercase}
.topbar .cell{position:absolute;top:0;height:42px;line-height:42px;padding:0 16px;border-left:1px solid rgba(255,255,255,.18)}
.topbar .cell:last-child{border-right:1px solid rgba(255,255,255,.18)}
.caret{display:inline-block;border:4px solid transparent;border-top-color:var(--white);margin-left:6px;vertical-align:-2px}
/* header */
.header{top:42px;height:109px;background:var(--white)}
.brand{position:absolute;left:97px;top:38px;display:flex;align-items:center;gap:10px}
.brand-dot{width:30px;height:30px;border-radius:50%;background:var(--blue-deep)}
.brand-name{font-family:"Raleway",sans-serif;font-weight:800;font-size:26px;color:var(--blue-deep);letter-spacing:1px}
.nav{position:absolute;right:97px;top:0;height:109px;display:flex;align-items:center;gap:21px;font-family:"Raleway",sans-serif;font-weight:600;font-size:12px;color:var(--ink);text-transform:uppercase}
.nav .active{color:var(--red)}
/* hero */
.hero{top:151px;height:524px}
.hero-photo{position:absolute;inset:0;background:linear-gradient(180deg,#5fb6d6 0%,#2a97c9 35%,#1f8bbf 55%,#d9cfb8 78%,#e8dcc2 100%)}
.hero-copy{position:absolute;left:659px;top:186px;width:400px;color:var(--white)}
.hero-title{font-family:"Raleway",sans-serif;font-weight:800;font-size:42px;letter-spacing:1px}
.hero-text{font-style:italic;font-size:13px;line-height:21px;margin-top:10px}
.hero-actions{display:flex;gap:20px;margin-top:24px}
.btn{display:inline-block;height:42px;line-height:38px;padding:0 26px;font-family:"Raleway",sans-serif;font-weight:700;font-size:13px;color:var(--white);border:2px solid var(--white);text-transform:uppercase}
.btn-book{background:var(--red)}
.hero-arrow{position:absolute;top:247px}
/* welcome */
.welcome{top:675px;height:379px}
.welcome-copy{position:absolute;left:97px;top:62px;width:540px}
.h2{font-family:"Raleway",sans-serif;font-weight:700;font-size:22px;color:var(--ink);text-transform:uppercase}
.welcome-lead{font-style:italic;color:var(--blue);font-size:13.5px;margin-top:12px}
.welcome-text{font-size:11.5px;line-height:23px;color:var(--grey-mid);margin-top:14px}
.read-more{display:inline-block;margin-top:14px;font-family:"Raleway",sans-serif;font-weight:700;font-size:11px;color:var(--red)}
.world-map{position:absolute;left:672px;top:28px;width:444px;height:288px;border-radius:50%/46%;background:radial-gradient(ellipse at 50% 45%,#6fc0ea 0%,#3e9fd8 60%,#2d7fb6 100%)}
/* services */
.services{top:1054px;height:309px}
.services-photo{position:absolute;inset:0;background:linear-gradient(180deg,#7fc3ea 0%,#cfe7f5 55%,#6b4327 59%,#4a2c19 100%)}
.service{position:absolute;top:101px;width:200px;margin-left:-100px;text-align:center}
.service-icon{width:120px;height:120px;margin:0 auto;border-radius:50%;background:var(--blue);border:4px solid var(--blue-dark);display:flex;align-items:center;justify-content:center}
.service-label{margin-top:24px;font-family:"Raleway",sans-serif;font-weight:700;font-size:13.5px;color:var(--white);text-transform:uppercase}
/* destinations */
.destinations{top:1363px;height:592px}
.dest-title{position:absolute;top:47px;width:100%;text-align:center}
.tabs{position:absolute;top:92px;width:100%;display:flex;justify-content:center;gap:16px;font-family:"Raleway",sans-serif;font-weight:600;font-size:12.5px;color:var(--grey-mid)}
.tabs .active{color:var(--red)}
.tabs .sep{color:var(--grey-light)}
.card{position:absolute;top:138px;width:302px;height:350px;border:1px solid var(--line);background:var(--white)}
.card-photo{position:absolute;left:6px;top:6px;width:288px;height:165px}
.card-body{position:absolute;left:16px;top:188px;right:16px}
.card-title{font-family:"Raleway",sans-serif;font-weight:700;font-size:14.5px;color:var(--ink);text-transform:uppercase}
.rating{display:flex;align-items:center;gap:2px;margin-top:6px;font-size:10.5px;color:var(--ink)}
.rating span{margin-left:8px}
.card-text{font-size:11.5px;line-height:21px;color:var(--grey-mid);margin-top:10px}
.card .read-more{margin-top:12px}
.view-more{position:absolute;left:549px;top:520px;width:102px;height:34px;line-height:30px;text-align:center;border:2px solid var(--grey-light);font-family:"Raleway",sans-serif;font-weight:700;font-size:11.5px;color:var(--grey-mid);text-transform:uppercase}
/* activity */
.activity{top:1955px;height:75px;background:var(--red-band)}
.activity-title{position:absolute;left:97px;top:24px;font-family:"Raleway",sans-serif;font-weight:800;font-size:22px;color:var(--white);text-transform:uppercase}
.activity-input{position:absolute;left:468px;top:20px;width:476px;height:36px;background:var(--white);border:1px solid #ddd}
.activity-input svg{position:absolute;left:14px;top:11px}
.activity-btn{position:absolute;left:971px;top:19px;width:103px;height:38px;line-height:38px;text-align:center;background:linear-gradient(#f2f2f2,#cfcfcf);font-family:"Raleway",sans-serif;font-weight:700;font-size:13px;color:var(--grey-mid);text-transform:uppercase}
/* footer */
.footer{top:2030px;height:228px;background:var(--blue);color:var(--white)}
.footer-col{position:absolute;top:42px}
.footer-head{font-family:"Raleway",sans-serif;font-weight:700;font-size:14.5px;text-transform:uppercase;margin-bottom:14px}
.footer-links{list-style:none;font-size:11.5px;line-height:24px}
.quick a{text-decoration:underline}
.social{display:grid;grid-template-columns:120px 120px;row-gap:12px;font-size:11.5px}
.social-item{display:flex;align-items:center;gap:12px}
.social-dot{width:28px;height:28px;border-radius:50%;background:var(--white);opacity:.95}
.contact-row{display:flex;align-items:center;gap:14px;font-size:11.5px;line-height:27px}
.contact-row svg{flex:none}
.copyright{top:2258px;height:62px;background:var(--blue-deep);color:var(--white);font-size:11px;text-align:center;line-height:62px}
</style>
</head>
<body>

<div class="section topbar">
  <div class="cell" style="left:100px">USD ( $ )<i class="caret"></i></div>
  <div class="cell" style="left:203px">English<i class="caret"></i></div>
  <div class="cell" style="left:672px">
    <svg width="12" height="9" viewBox="0 0 12 9" style="vertical-align:-1px;margin-right:6px"><rect width="12" height="9" fill="#fff"/><path d="M0 0l6 5 6-5" fill="none" stroke="#1b82c5" stroke-width="1.2"/></svg>Subscribe to our newsletter
  </div>
  <div class="cell" style="left:946px;padding:0 18px">Login&nbsp; / &nbsp;Register</div>
</div>

<header class="section header">
  <div class="brand"><span class="brand-dot"></span><span class="brand-name">VOYALIA</span></div>
  <nav class="nav">
    <a class="active" href="#">Home</a>
    <a href="#">Local Tour Company</a>
    <a href="#">Local Tour Guide</a>
    <a href="#">Transportation</a>
    <a href="#">Hotel/Flight</a>
    <a href="#">Activity</a>
    <a href="#">Contact Us</a>
    <svg width="12" height="12" viewBox="0 0 12 12"><circle cx="5" cy="5" r="3.6" fill="none" stroke="#474747" stroke-width="1.8"/><path d="M7.6 7.6L11 11" stroke="#474747" stroke-width="2"/></svg>
  </nav>
</header>

<section class="section hero">
  <div class="hero-photo" role="img" aria-label="Tropical beach with parasol and two deck chairs, turquoise sea, limestone islands and a hot air balloon"></div>
  <svg class="hero-arrow" style="left:36px" width="16" height="28" viewBox="0 0 16 28"><path d="M13 3L3 14l10 11" fill="none" stroke="#fff" stroke-width="3"/></svg>
  <svg class="hero-arrow" style="right:36px" width="16" height="28" viewBox="0 0 16 28"><path d="M3 3l10 11L3 25" fill="none" stroke="#fff" stroke-width="3"/></svg>
  <div class="hero-copy">
    <h1 class="hero-title">VOYALIA</h1>
    <p class="hero-text">At vero eos et accusamus et iusto odio dignissimos ducimus qui blanditiis praesentium voluptatum deleniti atque corrupti quos dolores et quaseleniti atqu..</p>
    <div class="hero-actions"><a class="btn btn-book" href="#">Book Now</a><a class="btn" href="#">Read More</a></div>
  </div>
</section>

<section class="section welcome">
  <div class="welcome-copy">
    <h2 class="h2">Welcome to Voyalia</h2>
    <p class="welcome-lead">At vero eos et accusamus et iusto odio dignissimos ducimus qui blanditiis</p>
    <p class="welcome-text">On the other hand, we denounce with righteous indignation and dislike men who are so be guiled and demoralized by the charms of pleasure of the moment, so blinded by desire, that they cannot foresee the pain and trouble that are bound to ensu.</p>
    <p class="welcome-text">Through shrinking from toil and pain. These cases are perfectly simple and easy to distinguish. In a free hour, when our power of choice is untrammelled and when nothing prevents our being able to do what we like best..</p>
    <a class="read-more" href="#">READ MORE &gt;&gt;</a>
  </div>
  <div class="world-map" role="img" aria-label="Illustrated blue disc with world landmarks labelled New York, England, Rome and Paris"></div>
</section>

<section class="section services">
  <div class="services-photo" role="img" aria-label="Blue sky above a wooden deck with leafy branch"></div>
  <div class="service" style="left:206px">
    <div class="service-icon"><svg width="60" height="60" viewBox="0 0 60 60" fill="#fff"><circle cx="32" cy="9" r="5"/><path d="M28 17h8l4 14-3 1-3-8-2 10 6 18h-5l-5-15-4 15h-5l5-22 1-9-4 6-4-1z"/><rect x="12" y="36" width="10" height="14" rx="1.5"/></svg></div>
    <div class="service-label">Selling Guided Tours</div>
  </div>
  <div class="service" style="left:402px">
    <div class="service-icon"><svg width="60" height="60" viewBox="0 0 60 60" fill="#fff"><rect x="18" y="16" width="24" height="34"/><g fill="#1b82c5"><rect x="22" y="20" width="4" height="4"/><rect x="28" y="20" width="4" height="4"/><rect x="34" y="20" width="4" height="4"/><rect x="22" y="28" width="4" height="4"/><rect x="28" y="28" width="4" height="4"/><rect x="34" y="28" width="4" height="4"/><rect x="22" y="36" width="4" height="4"/><rect x="34" y="36" width="4" height="4"/><rect x="27" y="42" width="6" height="8"/></g><path d="M20 10l1 2 2 .3-1.5 1.4.4 2.2L20 15l-1.9 1 .4-2.2L17 12.3l2-.3zM30 8l1 2 2 .3-1.5 1.4.4 2.2L30 13l-1.9 1 .4-2.2L27 10.3l2-.3zM40 10l1 2 2 .3-1.5 1.4.4 2.2L40 15l-1.9 1 .4-2.2L37 12.3l2-.3z"/><rect x="6" y="50" width="48" height="2"/></svg></div>
    <div class="service-label">Hotel</div>
  </div>
  <div class="service" style="left:600px">
    <div class="service-icon"><svg width="60" height="60" viewBox="0 0 60 60" fill="#fff"><path d="M50 14c3-3 0-6-3-3L37 20 14 14l-4 3 18 10-9 10-7-1-3 3 9 4 4 9 3-3-1-7 10-9 10 18 3-4-6-23z"/></svg></div>
    <div class="service-label">Flight</div>
  </div>
  <div class="service" style="left:796px">
    <div class="service-icon"><svg width="60" height="60" viewBox="0 0 60 60" fill="#fff"><circle cx="24" cy="11" r="5"/><rect x="28" y="9.5" width="16" height="3"/><rect x="38" y="12" width="3" height="4"/><path d="M16 28l4-8h20l4 8h2v14h-4v5h-6v-5H20v5h-6v-5h-4V28z"/><g fill="#1b82c5"><path d="M20 28l2.5-5h15l2.5 5z"/><circle cx="17" cy="35" r="2.5"/><circle cx="43" cy="35" r="2.5"/></g></svg></div>
    <div class="service-label">Rental Vehicles</div>
  </div>
  <div class="service" style="left:994px">
    <div class="service-icon"><svg width="64" height="60" viewBox="0 0 64 60" fill="#fff"><rect x="24" y="14" width="8" height="6"/><path d="M16 20h30v6H16z"/><path d="M6 27h52l-7 12H12z"/><g fill="#1b82c5"><rect x="19" y="22" width="3" height="2"/><rect x="25" y="22" width="3" height="2"/><rect x="31" y="22" width="3" height="2"/><rect x="37" y="22" width="3" height="2"/></g><path d="M4 44c5-3 9 3 14 0s9 3 14 0 9 3 14 0 9 3 14 0" fill="none" stroke="#fff" stroke-width="2.5"/></svg></div>
    <div class="service-label">Cruises</div>
  </div>
</section>

<section class="section destinations">
  <h2 class="h2 dest-title">Most Popular Destinations</h2>
  <div class="tabs"><span class="active">ALL</span><span class="sep">|</span><span>TOP</span><span class="sep">|</span><span>FEATURED</span><span class="sep">|</span><span>ALPHABETICAL A TO Z</span><span class="sep">|</span><span>MAP</span></div>

  <article class="card" style="left:99px">
    <div class="card-photo" role="img" aria-label="Rocky coastline with blue sea and cloudy sky" style="background:linear-gradient(180deg,#7fb4d8 0%,#4f8cb6 45%,#6f7f5a 70%,#8a8778 100%)"></div>
    <div class="card-body">
      <h3 class="card-title">Finibus Bonorum Lorum</h3>
      <div class="rating"><svg width="64" height="11" viewBox="0 0 64 11" fill="#e9a825"><path id="st" d="M5.5 0l1.6 3.5 3.8.4-2.9 2.5.9 3.7-3.4-2-3.4 2 .9-3.7L.1 3.9l3.8-.4z"/><use href="#st" x="13"/><use href="#st" x="26"/><use href="#st" x="39"/><use href="#st" x="52" opacity=".45"/></svg><span>( 190 REVIEWS )</span></div>
      <p class="card-text">Sed ut perspiciatis unde omnis iste error sit voluptatemveritatis arch beatae vitae dicta sunt explicabo. odit aut fugit..</p>
      <a class="read-more" href="#">READ MORE &gt;&gt;</a>
    </div>
  </article>

  <article class="card" style="left:449px">
    <div class="card-photo" role="img" aria-label="Outdoor pool framed by white marble columns" style="background:linear-gradient(180deg,#9cc3e0 0%,#d9dfe2 40%,#2f86c6 65%,#1f5e9a 100%)"></div>
    <div class="card-body">
      <h3 class="card-title">Finibus Bonorum Lorum</h3>
      <div class="rating"><svg width="64" height="11" viewBox="0 0 64 11" fill="#e9a825"><use href="#st"/><use href="#st" x="13"/><use href="#st" x="26"/><use href="#st" x="39"/><use href="#st" x="52" opacity=".45"/></svg><span>( 190 REVIEWS )</span></div>
      <p class="card-text">Sed ut perspiciatis unde omnis iste error sit voluptatemveritatis arch beatae vitae dicta sunt explicabo. odit aut fugit..</p>
      <a class="read-more" href="#">READ MORE &gt;&gt;</a>
    </div>
  </article>

  <article class="card" style="left:799px">
    <div class="card-photo" role="img" aria-label="Mountain valley under a hazy sunset sky" style="background:linear-gradient(180deg,#d8cdb6 0%,#b59a7a 40%,#7a5a40 70%,#4e3624 100%)"></div>
    <div class="card-body">
      <h3 class="card-title">Finibus Bonorum Lorum</h3>
      <div class="rating"><svg width="64" height="11" viewBox="0 0 64 11" fill="#e9a825"><use href="#st"/><use href="#st" x="13"/><use href="#st" x="26"/><use href="#st" x="39"/><use href="#st" x="52" opacity=".45"/></svg><span>( 190 REVIEWS )</span></div>
      <p class="card-text">Sed ut perspiciatis unde omnis iste error sit voluptatemveritatis arch beatae vitae dicta sunt explicabo. odit aut fugit..</p>
      <a class="read-more" href="#">READ MORE &gt;&gt;</a>
    </div>
  </article>

  <a class="view-more" href="#">View More</a>
</section>

<section class="section activity">
  <h2 class="activity-title">Find your next activity!</h2>
  <div class="activity-input"><svg width="13" height="13" viewBox="0 0 12 12"><circle cx="5" cy="5" r="3.6" fill="none" stroke="#aaaaaa" stroke-width="1.6"/><path d="M7.6 7.6L11 11" stroke="#aaaaaa" stroke-width="1.8"/></svg></div>
  <a class="activity-btn" href="#">Search</a>
</section>

<footer class="section footer">
  <div class="footer-col quick" style="left:99px">
    <h4 class="footer-head">Quick Links</h4>
    <ul class="footer-links"><li><a href="#">About Us</a></li><li><a href="#">Corporate Info</a></li><li><a href="#">Careers</a></li><li><a href="#">Site Map</a></li><li><a href="#">Free Newsletter</a></li></ul>
  </div>
  <div class="footer-col" style="left:312px">
    <h4 class="footer-head">Info &amp; Help</h4>
    <ul class="footer-links"><li>Customer Care</li><li>Privacy Policy</li><li>Low Price Guarantee</li><li>Group Services</li><li>Mileage Program</li></ul>
  </div>
  <div class="footer-col" style="left:543px">
    <h4 class="footer-head">Share Your Adventure</h4>
    <div class="social">
      <div class="social-item"><span class="social-dot"></span>Friendwall</div>
      <div class="social-item"><span class="social-dot"></span>Blogbox</div>
      <div class="social-item"><span class="social-dot"></span>Circleup</div>
      <div class="social-item"><span class="social-dot"></span>Pinboard</div>
      <div class="social-item"><span class="social-dot"></span>Clipcast</div>
    </div>
  </div>
  <div class="footer-col" style="left:897px">
    <h4 class="footer-head">Contact Us</h4>
    <div class="contact-row"><svg width="12" height="14" viewBox="0 0 12 16" fill="#fff"><path d="M6 0a6 6 0 016 6c0 4-6 10-6 10S0 10 0 6a6 6 0 016-6z"/><circle cx="6" cy="6" r="2.2" fill="#1b82c5"/></svg>48 Harbor Lane, Fairview, NJ, 07022</div>
    <div class="contact-row"><svg width="12" height="14" viewBox="0 0 10 16" fill="#fff"><rect width="10" height="16" rx="2"/><rect x="2" y="2" width="6" height="10" fill="#1b82c5"/></svg>1 800 555 0142</div>
    <div class="contact-row"><svg width="12" height="14" viewBox="0 0 14 14" fill="#fff"><rect x="0" y="4" width="14" height="10" rx="1.5"/><rect x="3" y="0" width="8" height="5"/><rect x="3" y="7" width="8" height="2" fill="#1b82c5"/></svg>1 800 555 0177</div>
    <div class="contact-row"><svg width="14" height="12" viewBox="0 0 14 10"><rect width="14" height="10" fill="#fff"/><path d="M0 0l7 5.5L14 0" fill="none" stroke="#1b82c5" stroke-width="1.3"/></svg><a href="#" style="text-decoration:underline">hello@voyalia.in</a></div>
  </div>
</footer>

<div class="section copyright">Copyright © 2015 . Voyalia . All rights reserved .</div>

</body>
</html>
```